It must be unique & Proffessional
VORNA GROUP
# 130 Very nice, could you please use the “symbols” for Phone, cellphone and so on, instead of writing “p:” and “c:”. You did that by # 69 :-)
Thanks for all your very creative suggestions.
A general comment:
- Please correct the “projektchef” to “Direktør”
- Please add at fixed telephone number +45 62 18 37 95
- Please add “+45” in front of the cellphone number
- Please make the envelope as window envelops, and logo bottom right corner
- On the A4 paper, we need the logo in top right corner
#61,Very good design, please make the backside as you’ve done by #64
#128Please leave the bottom of the paper free of text and colors, and add only one thin line 13 mm from the page bottom.
Again very good designs, thank you very much
Logo AI file is now uploaded :-)
Now we have our Logo ready, looking forward to see your suggestions for design :-)
KT/VRG Team
Logo is currently being designed, you can participate if you would like to :-)

```html
<!DOCTYPE html>
<html lang="da">
<head>
<meta charset="utf-8">
<title>Vorna Group – Visitkort</title>
<link rel="stylesheet" href="https://fonts.googleapis.com/css2?family=Open+Sans:wght@400;600;800&display=swap">
<style>
  :root {
    --backdrop: #e9e7e3;
    --card-white: #ffffff;
    --card-dark: #3d4747;
    --accent-red: #c8312b;
    --text-dark: #4a4f52;
    --text-muted: #6d7275;
    --text-light: #f2f4f4;
  }
  * { box-sizing: border-box; margin: 0; padding: 0; }
  html, body {
    width: 1200px; height: 530px; overflow: hidden;
    background: var(--backdrop);
    font-family: "Open Sans", Arial, sans-serif;
  }
  .stage { position: relative; width: 1200px; height: 530px; }
  .card {
    position: absolute; width: 552px; height: 318px;
    box-shadow: 0 6px 18px rgba(0,0,0,.22);
  }
  .card-front { left: 24px; top: 102px; background: var(--card-white); }
  .card-back { left: 612px; top: 98px; background: var(--card-dark); }

  .front-stripe {
    position: absolute; left: 0; top: 0; width: 7px; height: 100%;
    background: var(--accent-red);
  }
  .brand {
    position: absolute; left: 42px; top: 84px;
    display: flex; align-items: center; gap: 10px;
  }
  .brand-square { width: 26px; height: 26px; background: var(--accent-red); }
  .brand-name {
    font-weight: 800; font-size: 30px; letter-spacing: 0.5px;
    color: var(--text-dark);
  }
  .holder { position: absolute; right: 34px; top: 160px; text-align: right; }
  .holder-name { font-size: 17px; color: var(--accent-red); letter-spacing: 0.4px; }
  .holder-role { font-size: 13px; color: var(--text-muted); margin-top: 2px; }
  .contact {
    position: absolute; left: 34px; right: 34px; bottom: 28px;
    font-size: 12px; color: var(--text-muted); text-align: right; line-height: 1.75;
  }
  .contact-row { display: flex; justify-content: flex-end; gap: 18px; }
  .contact-item { display: inline-flex; align-items: center; gap: 6px; }
  .contact-icon { width: 11px; height: 11px; fill: var(--accent-red); flex: none; }

  .back-brand {
    position: absolute; left: 0; right: 0; top: 104px;
    display: flex; justify-content: center; align-items: center; gap: 12px;
  }
  .back-brand .brand-square { background: var(--text-light); width: 30px; height: 30px; }
  .back-brand .brand-name { color: var(--text-light); font-size: 34px; }
  .back-web {
    position: absolute; left: 0; right: 0; bottom: 64px; text-align: center;
    color: var(--text-light); font-size: 13px; letter-spacing: 2.5px;
  }
</style>
</head>
<body>
<div class="stage">
  <section class="card card-front">
    <div class="front-stripe"></div>
    <div class="brand">
      <span class="brand-square"></span>
      <span class="brand-name">VORNA GROUP</span>
    </div>
    <div class="holder">
      <p class="holder-name">MIKKEL HAUGSTED</p>
      <p class="holder-role">Direktør</p>
    </div>
    <div class="contact">
      <p>Vestergade 42, &nbsp;7100 Vejle, Denmark</p>
      <p class="contact-row">
        <span class="contact-item">
          <svg class="contact-icon" viewBox="0 0 12 12" aria-label="Telefon"><path d="M2.4 0.6 L4.2 0.6 L5 3.2 L3.8 4.2 C4.5 5.8 6.2 7.5 7.8 8.2 L8.8 7 L11.4 7.8 L11.4 9.6 C11.4 10.7 10.6 11.4 9.6 11.4 C4.6 11.1 0.9 7.4 0.6 2.4 C0.6 1.4 1.3 0.6 2.4 0.6 Z"/></svg>
          +45 62 18 37 95
        </span>
        <span class="contact-item">
          <svg class="contact-icon" viewBox="0 0 12 12" aria-label="Mobil"><path d="M3.2 0 H8.8 C9.4 0 9.8 0.4 9.8 1 V11 C9.8 11.6 9.4 12 8.8 12 H3.2 C2.6 12 2.2 11.6 2.2 11 V1 C2.2 0.4 2.6 0 3.2 0 Z M3.4 1.4 V9.4 H8.6 V1.4 Z M6 10 A0.7 0.7 0 1 0 6 11.4 A0.7 0.7 0 1 0 6 10 Z"/></svg>
          +45 4816 2039
        </span>
      </p>
      <p class="contact-row">
        <span class="contact-item">
          <svg class="contact-icon" viewBox="0 0 12 12" aria-label="E-mail"><path d="M0 2 H12 V10 H0 Z M1 3 V3.4 L6 6.6 L11 3.4 V3 Z M1 4.6 V9 H11 V4.6 L6 7.8 Z" fill-rule="evenodd"/></svg>
          mh@vornagroup.com
        </span>
        <span class="contact-item">
          <svg class="contact-icon" viewBox="0 0 12 12" aria-label="Web"><path d="M6 0 A6 6 0 1 0 6 12 A6 6 0 1 0 6 0 Z M6 1.2 C6.8 2 7.3 3.4 7.4 5.4 H4.6 C4.7 3.4 5.2 2 6 1.2 Z M1.2 6.6 H3.4 C3.5 8.2 3.8 9.5 4.3 10.5 C2.7 9.9 1.5 8.4 1.2 6.6 Z M1.2 5.4 C1.5 3.6 2.7 2.1 4.3 1.5 C3.8 2.5 3.5 3.8 3.4 5.4 Z M4.6 6.6 H7.4 C7.3 8.6 6.8 10 6 10.8 C5.2 10 4.7 8.6 4.6 6.6 Z M8.6 6.6 H10.8 C10.5 8.4 9.3 9.9 7.7 10.5 C8.2 9.5 8.5 8.2 8.6 6.6 Z M8.6 5.4 C8.5 3.8 8.2 2.5 7.7 1.5 C9.3 2.1 10.5 3.6 10.8 5.4 Z"/></svg>
          www.vornagroup.com
        </span>
      </p>
    </div>
  </section>

  <section class="card card-back">
    <div class="back-brand">
      <span class="brand-square"></span>
      <span class="brand-name">VORNA GROUP</span>
    </div>
    <p class="back-web">www.vornagroup.com</p>
  </section>
</div>
</body>
</html>
```